Business Card Design

Looking for business card designs for a new business. there will be two cards of the same design (both lots of information below in contact info). We would like the logo diagonally across the card with the information split above and below the logo similar to sketch. happy to look at similar alternatives
Please use same colours as in logo design

Industry/Entity Type

Business

Contact Information for Business Card

Dwight Halloran
mob - 0491 738 204
ph - 02 6148 3920
fax - 02 6148 3975
email - dwight@kestrelbeams.com.au
14 Larkmoor Road, Taminda NSW 2340

Colin Marchetti
mob - 0438 912 557
ph - 02 6148 3920
fax - 02 6148 3975
email - colin@kestrelbeams.com.au

```html
<!DOCTYPE html>
<html lang="en">
<head>
<meta charset="utf-8">
<title>Kestrel Beams – Business Cards</title>
<link href="https://fonts.googleapis.com/css2?family=Source+Sans+3:wght@400;600;700&display=swap" rel="stylesheet">
<style>
  :root {
    --backdrop: #e6e4df;
    --card-white: #ffffff;
    --card-black: #000000;
    --teal: #0b7f7a;
    --mist: #c9dcdc;
    --ink: #2a2a2a;
    --paper-edge: #8a8a8a;
  }
  * { margin: 0; padding: 0; box-sizing: border-box; }
  html, body {
    width: 1145px; height: 1200px; overflow: hidden;
    background: var(--backdrop);
    font-family: "Source Sans 3", "Myriad Pro", Arial, sans-serif;
  }
  .canvas { position: relative; width: 1145px; height: 1200px; }

  .card {
    position: absolute; width: 944px; height: 539px; overflow: hidden;
    box-shadow: 0 4px 14px rgba(0,0,0,.18);
  }
  .card-front { left: 17px; top: 26px; background: var(--card-white); border: 1px solid var(--paper-edge); }
  .card-back { left: 182px; top: 621px; background: var(--card-black); }

  .wordmark {
    display: flex; align-items: center; gap: 16px;
    color: var(--teal); font-weight: 700; line-height: 1; white-space: nowrap;
  }
  .wordmark-square { background: var(--teal); flex: none; }

  .card-front .wordmark { position: absolute; left: 22px; top: 78px; font-size: 76px; }
  .card-front .wordmark-square { width: 52px; height: 52px; }

  .contact-list { position: absolute; left: 22px; top: 226px; list-style: none; }
  .contact-item {
    display: flex; align-items: center; gap: 6px; height: 36px;
    font-size: 23px; color: var(--ink);
  }
  .contact-icon { width: 20px; height: 20px; flex: none; fill: var(--teal); }

  .address { position: absolute; left: 22px; top: 396px; font-size: 23px; color: var(--ink); }

  .name-band {
    position: absolute; left: 0; right: 0; bottom: 0; height: 70px;
    background: var(--mist); display: flex; align-items: center; padding-left: 20px;
  }
  .holder-name { font-size: 29px; font-weight: 700; color: var(--ink); }

  .card-back .wordmark {
    position: absolute; left: 0; right: 0; top: 200px; justify-content: center;
    font-size: 100px;
  }
  .card-back .wordmark-square { width: 70px; height: 70px; }

  .website {
    position: absolute; left: 0; right: 0; top: 428px; text-align: center;
    color: #ffffff; font-size: 29px; letter-spacing: 2.5px;
  }
</style>
</head>
<body>
<main class="canvas">

  <section class="card card-front" aria-label="Business card front">
    <div class="wordmark"><span class="wordmark-square"></span>Kestrel Beams</div>

    <ul class="contact-list">
      <li class="contact-item">
        <svg class="contact-icon" viewBox="0 0 20 20" aria-label="Phone"><path d="M4 2l3 0 2 5-2 1.5c1 2.2 2.4 3.6 4.5 4.5L13 11l5 2v3c0 1-1 2-2 2C8.5 18 2 11.5 2 4c0-1 1-2 2-2z"/></svg>
        <span>02 6148 3920</span>
      </li>
      <li class="contact-item">
        <svg class="contact-icon" viewBox="0 0 20 20" aria-label="Mobile"><path d="M6 1h8a1.5 1.5 0 0 1 1.5 1.5v15A1.5 1.5 0 0 1 14 19H6a1.5 1.5 0 0 1-1.5-1.5v-15A1.5 1.5 0 0 1 6 1zm0.5 2.5v10h7v-10zM10 15a1.2 1.2 0 1 0 0 2.4A1.2 1.2 0 0 0 10 15z"/></svg>
        <span>0438 912 557</span>
      </li>
      <li class="contact-item">
        <svg class="contact-icon" viewBox="0 0 20 20" aria-label="Fax"><path d="M5 3h8l2 2v3H5zM2 9h16v7h-3v-3H5v3H2zM6 14h8v4H6z"/></svg>
        <span>02 6148 3975</span>
      </li>
      <li class="contact-item">
        <svg class="contact-icon" viewBox="0 0 20 20" aria-label="Email"><path d="M2 8l8-5 8 5v9H2zm2 1.2l6 4 6-4-6-3.8z"/></svg>
        <span>colin@kestrelbeams.com.au</span>
      </li>
    </ul>

    <p class="address">14 Larkmoor Road, Brackenvale NSW 2361</p>

    <div class="name-band"><span class="holder-name">Colin Marchetti</span></div>
  </section>

  <section class="card card-back" aria-label="Business card back">
    <div class="wordmark"><span class="wordmark-square"></span>Kestrel Beams</div>
    <p class="website">www.kestrelbeams.com.au</p>
  </section>

</main>
</body>
</html>
```